Logo Tweaks & Stationery Design Project for Energy Management Co

We are a specialist metering company trading for over 60 years and have recently developed GPRS metering infrastructure & monitoring services. For more information please see http://www.kestrel-vale.example/remote-meter-reading.html

Due to the success of this system it’s become necessary to open a new company “Brightwell Gauge Ltd” and this project is for relevant stationary designs for our documents.

I need something modern and clear to match our new logo style. Feel free to play around with the colors and tweak the logo if you like.

Maybe with some line chart animation on the header relating to our online services. ( See inspiration file )

Thanks
Derek

Target Market(s)

Renewable Energy Generation Monitoring, Energy Management, Remote Monitoring and Tennant Billing.

Industry/Entity Type

It Company

Requirements
Nice to have
• 100% Carbon neutral hosting
Should not have
• "Clip-Art" should not be used.

```html
<!DOCTYPE html>
<html lang="en">
<head>
<meta charset="utf-8">
<title>Brightwell Gauge Ltd — Letterhead</title>
<link rel="stylesheet" href="https://fonts.googleapis.com/css2?family=Michroma&display=swap">
<style>
  :root {
    --backdrop: #e9e7e3;
    --paper: #ffffff;
    --navy: #2b3990;
    --brand-blue: #2e3192;
    --sky: #1c75bc;
    --glow: #b4cbea;
    --cyan: #29aae2;
    --leaf: #8dc63f;
    --forest: #129a48;
    --stripe: #8a8a8a;
    --accent-red: #c4161c;
  }
  * { margin: 0; padding: 0; box-sizing: border-box; }
  html, body {
    width: 960px;
    height: 1200px;
    overflow: hidden;
    background: var(--backdrop);
  }
  .canvas {
    position: relative;
    width: 960px;
    height: 1200px;
  }
  .letterhead {
    position: absolute;
    left: 70px;
    top: 20px;
    width: 820px;
    height: 1160px;
    background: var(--paper);
    box-shadow: 0 4px 14px rgba(0, 0, 0, 0.25);
    overflow: hidden;
  }
  .letterhead svg { display: block; }
  .wordmark {
    font-family: "Michroma", sans-serif;
    fill: var(--brand-blue);
  }
  .footer-name {
    font-family: "Michroma", sans-serif;
    fill: var(--brand-blue);
    letter-spacing: 2px;
  }
  .footer-mark {
    font-family: "Michroma", sans-serif;
    fill: var(--paper);
  }
</style>
</head>
<body>
<main class="canvas">
  <section class="letterhead" aria-label="Brightwell Gauge Ltd letterhead">
    <svg width="820" height="1160" viewBox="0 0 820 1160" xmlns="http://www.w3.org/2000/svg">
      <defs>
        <linearGradient id="header-sweep" x1="0" y1="0" x2="1" y2="0">
          <stop offset="0" stop-color="var(--navy)"/>
          <stop offset="0.28" stop-color="var(--navy)"/>
          <stop offset="0.4" stop-color="var(--sky)"/>
          <stop offset="0.46" stop-color="var(--glow)"/>
          <stop offset="0.56" stop-color="var(--sky)"/>
          <stop offset="0.75" stop-color="var(--navy)"/>
          <stop offset="1" stop-color="var(--navy)"/>
        </linearGradient>
        <linearGradient id="header-leaf" x1="0" y1="0" x2="1" y2="0">
          <stop offset="0" stop-color="var(--forest)"/>
          <stop offset="1" stop-color="var(--leaf)"/>
        </linearGradient>
        <linearGradient id="footer-leaf" x1="0" y1="0" x2="1" y2="0">
          <stop offset="0" stop-color="var(--leaf)"/>
          <stop offset="0.5" stop-color="var(--forest)"/>
          <stop offset="1" stop-color="var(--leaf)"/>
        </linearGradient>
        <linearGradient id="footer-band" x1="0" y1="0" x2="1" y2="0">
          <stop offset="0" stop-color="var(--cyan)"/>
          <stop offset="0.55" stop-color="var(--sky)"/>
          <stop offset="1" stop-color="var(--navy)"/>
        </linearGradient>
        <clipPath id="stripe-field">
          <path d="M300,128 Q500,42 820,36 V140 H300 Z"/>
        </clipPath>
      </defs>

      <!-- header band -->
      <rect class="header-band" x="0" y="0" width="820" height="420" fill="url(#header-sweep)"/>

      <!-- striped field behind the header swoosh -->
      <g class="header-stripes" clip-path="url(#stripe-field)">
        <rect x="300" y="30" width="520" height="110" fill="var(--paper)"/>
        <g stroke="var(--stripe)" stroke-width="2.5">
          <line x1="300" y1="46" x2="820" y2="46"/>
          <line x1="300" y1="55" x2="820" y2="55"/>
          <line x1="300" y1="64" x2="820" y2="64"/>
          <line x1="300" y1="73" x2="820" y2="73"/>
          <line x1="300" y1="82" x2="820" y2="82"/>
          <line x1="300" y1="91" x2="820" y2="91"/>
          <line x1="300" y1="100" x2="820" y2="100"/>
          <line x1="300" y1="109" x2="820" y2="109"/>
          <line x1="300" y1="118" x2="820" y2="118"/>
        </g>
      </g>

      <!-- header swoosh -->
      <path class="header-swoosh" d="M180,124 Q440,62 820,108 V250 Q560,110 180,124 Z" fill="url(#header-leaf)"/>

      <!-- footer swoosh base -->
      <path class="footer-swoosh" d="M0,900 Q420,1090 820,905 V1160 H0 Z" fill="url(#footer-leaf)"/>

      <!-- writing area -->
      <ellipse class="writing-area" cx="415" cy="600" rx="690" ry="490" fill="var(--paper)"/>

      <!-- footer divider and band -->
      <path class="footer-divider" d="M0,1098 Q440,1128 820,1046" fill="none" stroke="var(--paper)" stroke-width="10"/>
      <path class="footer-band" d="M0,1108 Q450,1128 820,1054 V1160 H0 Z" fill="url(#footer-band)"/>

      <!-- brand name in header -->
      <text class="wordmark" x="430" y="122" font-size="62">BGL</text>
      <circle class="wordmark-dot" cx="706" cy="102" r="12" fill="var(--accent-red)"/>

      <!-- footer name and mark -->
      <text class="footer-name" x="28" y="1148" font-size="22">BRIGHTWELL GAUGE</text>
      <text class="footer-mark" x="672" y="1146" font-size="30">BGL</text>
    </svg>
  </section>
</main>
</body>
</html>
```